Business cards to launch an education platform

Hi,
I am looking at having new business cards designed.
I am a startup, developing a web platform for schools and university, the education world. It's an online assessment system.
I would like a card that looks classy, and that is using the colors and the font of my logo.

I have attached:
1) my logo
2) A business card that I have designed quickly so you can have all the information required in the card, but I really don't like it.
3) The font that I am using (Lato Regular) to design my web platform
4) Some screenshots of my web platform so you can have a look at the style that I have.

Target Market(s)

Major market: Education system: Schools and university
Minor markets: Business in general

Industry/Entity Type

Business

Contact Information for Business Card

Clara Fenwick
Director

M: 0437 518 902
E: clara.fenwick@amberLoomSystems.com.au

Requirements
Must have
• The colors of my logo

```html
<!DOCTYPE html>
<html lang="en">
<head>
<meta charset="utf-8">
<title>Amber Loom Systems – Business Cards</title>
<link rel="stylesheet" href="https://fonts.googleapis.com/css2?family=Exo+2:wght@400;600&family=Lato:wght@400&display=swap">
<style>
  :root {
    --backdrop: #c9baa8;
    --card: #ffffff;
    --brand-blue: #1b8ad0;
    --brand-deep: #0f6fb0;
    --brand-light: #5ec8f0;
    --ink: #3a3a3a;
    --ink-soft: #555555;
  }
  * { margin: 0; padding: 0; box-sizing: border-box; }
  html, body { width: 1200px; height: 763px; overflow: hidden; }
  body { background: var(--backdrop); position: relative; font-family: "Exo 2", sans-serif; }

  .card {
    position: absolute; top: 230px; width: 503px; height: 290px;
    background: var(--card);
    box-shadow: 0 2px 8px rgba(0,0,0,0.25);
    overflow: hidden;
  }
  .card--front { left: 98px; }
  .card--back { left: 608px; }

  .ribbon { position: absolute; left: 307px; top: 0; width: 174px; height: 168px; }

  .holder { position: absolute; left: 11px; top: 73px; }
  .holder__name { font-size: 18px; font-weight: 600; color: var(--brand-deep); letter-spacing: 0.5px; text-transform: uppercase; line-height: 1; }
  .holder__title { font-size: 6px; color: var(--ink); text-transform: uppercase; letter-spacing: 0.3px; margin-top: 3px; }

  .contacts { position: absolute; left: 12px; top: 150px; list-style: none; }
  .contacts li { display: flex; align-items: center; height: 22px; font-size: 14px; color: var(--ink); letter-spacing: 0.6px; white-space: nowrap; }
  .contacts li.contacts__small { font-size: 10.5px; letter-spacing: 0.2px; }
  .contacts li.contacts__address { font-size: 8px; letter-spacing: 0.2px; }
  .contacts svg { width: 13px; height: 13px; margin-right: 8px; flex: none; }

  .brand { position: absolute; display: flex; align-items: center; }
  .brand__mark { background: var(--brand-blue); flex: none; }
  .brand__name { font-family: "Lato", sans-serif; font-weight: 400; color: var(--brand-blue); text-transform: uppercase; line-height: 1.05; letter-spacing: 1px; }

  .brand--front { left: 290px; top: 198px; }
  .brand--front .brand__mark { width: 50px; height: 50px; margin-right: 10px; }
  .brand--front .brand__name { font-size: 17px; }

  .brand--back { left: 95px; top: 98px; }
  .brand--back .brand__mark { width: 94px; height: 94px; margin-right: 16px; }
  .brand--back .brand__name { font-size: 28px; }
</style>
</head>
<body>
  <section class="card card--front">
    <svg class="ribbon" viewBox="0 0 174 168">
      <defs>
        <radialGradient id="ribbonFill" cx="50%" cy="45%" r="60%">
          <stop offset="0" stop-color="#2ea3e3"/>
          <stop offset="1" stop-color="#0f6fb0"/>
        </radialGradient>
      </defs>
      <polygon points="0,0 174,0 174,148 87,108 0,148" fill="url(#ribbonFill)"/>
      <polyline points="0,158 87,118 174,158" fill="none" stroke="#5ec8f0" stroke-width="8"/>
    </svg>

    <div class="holder">
      <p class="holder__name">Clara Fenwick</p>
      <p class="holder__title">Director</p>
    </div>

    <ul class="contacts">
      <li><svg viewBox="0 0 14 14"><circle cx="7" cy="7" r="7" fill="#1b8ad0"/><rect x="4.5" y="3" width="5" height="8" rx="1" fill="#fff"/></svg>0437 518 902</li>
      <li><svg viewBox="0 0 14 14"><circle cx="7" cy="7" r="7" fill="#1b8ad0"/><path d="M4 4.5c0 3 2.5 5.5 5.5 5.5l1-1.5-1.8-1-0.8 0.8c-1-0.5-1.7-1.2-2.2-2.2l0.8-0.8-1-1.8z" fill="#fff"/></svg>0437 518 902</li>
      <li class="contacts__small"><svg viewBox="0 0 14 14"><circle cx="7" cy="7" r="7" fill="#1b8ad0"/><rect x="3.5" y="4.5" width="7" height="5" fill="#fff"/><polyline points="3.5,4.5 7,7.5 10.5,4.5" fill="none" stroke="#1b8ad0" stroke-width="0.8"/></svg>clara.fenwick@amberLoomSystems.com.au</li>
      <li class="contacts__small"><svg viewBox="0 0 14 14"><circle cx="7" cy="7" r="7" fill="#1b8ad0"/><circle cx="7" cy="7" r="3.5" fill="none" stroke="#fff" stroke-width="1"/><line x1="3.5" y1="7" x2="10.5" y2="7" stroke="#fff" stroke-width="0.8"/></svg>www.amberloomsystems.com.au</li>
      <li class="contacts__address"><svg viewBox="0 0 14 14"><circle cx="7" cy="7" r="7" fill="#1b8ad0"/><path d="M7 3a2.7 2.7 0 0 1 2.7 2.7C9.7 8 7 11 7 11S4.3 8 4.3 5.7A2.7 2.7 0 0 1 7 3z" fill="#fff"/><circle cx="7" cy="5.7" r="1" fill="#1b8ad0"/></svg>14 Harbour Lane, Level 3, Sydney</li>
    </ul>

    <div class="brand brand--front">
      <span class="brand__mark"></span>
      <p class="brand__name">Amber Loom<br>Systems</p>
    </div>
  </section>

  <section class="card card--back">
    <div class="brand brand--back">
      <span class="brand__mark"></span>
      <p class="brand__name">Amber Loom<br>Systems</p>
    </div>
  </section>
</body>
</html>
```